Brickfield real estate investment company needs a poster design

We would like a poster design size 18 x 24.
Poster wording -
I WANT TO BUY YOUR ( finish with logo) logo uploaded
website- www.brickfield.example
phone # 555-218-7043 ( color red for the phone number)
we would like to see the poster on 2 different backgrounds
Yellow background
White background
horizontal

```html
<!DOCTYPE html>
<html lang="en">
<head>
<meta charset="utf-8">
<title>Brickfield – I Want To Buy Your House</title>
<link rel="stylesheet" href="https://fonts.googleapis.com/css2?family=Oswald:wght@500&family=Rubik:wght@500;800&display=swap">
<style>
  :root {
    --red: #e31e24;
    --yellow: #ffef00;
    --black: #000000;
    --white: #ffffff;
  }
  html, body {
    margin: 0;
    padding: 0;
    overflow: hidden;
    background: var(--white);
  }
  .poster {
    display: block;
    width: 1200px;
    height: 900px;
  }
  .band-red { fill: var(--red); }
  .band-yellow { fill: var(--yellow); }
  .wave-black { fill: var(--black); }
  .headline {
    font-family: "Oswald", "Arial Narrow", sans-serif;
    font-weight: 500;
    fill: var(--white);
  }
  .brand-name {
    font-family: "Rubik", Arial, sans-serif;
    font-weight: 800;
    fill: var(--black);
  }
  .website {
    font-family: "Rubik", Arial, sans-serif;
    font-weight: 500;
    fill: var(--black);
  }
  .phone-badge { fill: var(--white); }
  .phone-icon { fill: var(--black); }
  .phone-number {
    font-family: "Rubik", Arial, sans-serif;
    font-weight: 500;
    fill: var(--white);
  }
</style>
</head>
<body>
<svg class="poster" viewBox="0 0 1200 900" xmlns="http://www.w3.org/2000/svg" role="img" aria-label="I want to buy your house – Brickfield poster">
  <rect class="band-yellow" x="0" y="0" width="1200" height="900"/>

  <!-- top red band -->
  <path class="band-red" d="M0,0 H1200 V220 C1100,245 1000,255 900,246 C780,238 700,220 600,192 C450,150 250,140 0,238 Z"/>

  <!-- black wave and bottom red band -->
  <path class="wave-black" d="M0,696 C200,590 400,600 600,630 C800,660 1000,700 1200,652 V900 H0 Z"/>
  <path class="band-red" d="M0,832 C60,770 120,730 180,700 C320,632 470,636 600,650 C800,672 1000,735 1200,680 V900 H0 Z"/>

  <text class="headline" x="40" y="182" font-size="200" textLength="1130" lengthAdjust="spacingAndGlyphs">I WANT TO BUY YOUR</text>

  <text class="brand-name" x="50" y="468" font-size="150" textLength="1062" lengthAdjust="spacingAndGlyphs">BRICKFIELD</text>
  <text class="website" x="413" y="538" font-size="62" textLength="695" lengthAdjust="spacingAndGlyphs">www.brickfield.example</text>

  <circle class="phone-badge" cx="124" cy="779" r="78"/>
  <path class="phone-icon" d="M98,730 l8,-6 q4,-2 6,1 l16,24 q2,3 -1,6 l-8,5 q-2,2 0,6 q6,18 22,30 q3,2 5,0 l7,-6 q3,-2 5,1 l16,24 q2,4 -2,7 q-6,4 -14,3 q-30,-6 -52,-36 q-20,-30 -14,-58 q2,-5 6,-7 Z"/>

  <text class="phone-number" x="230" y="852" font-size="175" textLength="930" lengthAdjust="spacingAndGlyphs">555-218-7043</text>
</svg>
</body>
</html>
```